Form With Marla - Health and Wellness Business Card and Logo

I need a business card design with a logo for my business you can check out at www.formwithmarla.net. I want something more original, simplistic, and memorable than the basic logo I have on my site currently. I am a health and wellness coach and I offer mindset coaching and nutrition plans. I like the colour teal and dark grey/black for my theme colours. I emphasize growth, longterm change, and the whole package of "healthy mind, healthy body, healthy life". I had played around the idea of intertwining 3 M's or incorporating growth (leaves etc.) into my design. I want my expertise and experience to show through. In one glance I want people to understand with confidence I can help them accomplish anything they set their minds to. I look forward to seeing what everyone comes up with!

Industry/Entity Type

Health And Wellness

Contact Information for Business Card

Form With Marla
Marla Prentiss
BSc, Health & Wellness Coach
"Manifest your best"
www.formwithmarla.net
formwithmarla@quillpost.net
472-618-9043

Colors
33b8a4
ffffff
333333
000000

Requirements
Must have
• A memorable and unique logo for my business!
Nice to have
• Could have the phrase "Are you unhappy with your body and state of health?" or "It takes the right skills to develop habits in order to create long term change. I can help you get there."

```html
<!DOCTYPE html>
<html lang="en">
<head>
<meta charset="utf-8">
<title>Form With Marla – Business Card</title>
<link rel="stylesheet" href="https://fonts.googleapis.com/css2?family=Open+Sans:wght@400;700&display=swap">
<style>
  :root {
    --stage: #d9d9d9;
    --card-dark: #1f1f1f;
    --card-light: #ffffff;
    --ink: #333333;
    --ink-soft: #555555;
    --rule: #6a6a6a;
    --teal: #33b8a4;
    --on-dark: #ffffff;
  }
  * { margin: 0; padding: 0; box-sizing: border-box; }
  html, body {
    width: 1200px; height: 1000px; overflow: hidden;
    background: var(--stage);
    font-family: "Open Sans", Arial, sans-serif;
  }
  .canvas { position: relative; width: 1200px; height: 1000px; }
  .card {
    position: absolute; left: 220px; width: 760px; height: 434px;
    border-radius: 22px;
    box-shadow: 0 8px 24px rgba(0,0,0,0.18);
  }
  .card--back { top: 41px; background: var(--card-dark); }
  .card--front { top: 525px; background: var(--card-light); }

  .brand {
    position: absolute; display: flex; align-items: center; gap: 12px;
    font-weight: 400; letter-spacing: 0.5px; white-space: nowrap;
  }
  .brand__mark { display: block; width: 16px; height: 16px; background: var(--teal); }
  .card--back .brand {
    left: 50%; top: 50%; transform: translate(-50%, -50%);
    color: var(--on-dark); font-size: 40px;
  }
  .card--front .brand {
    right: 62px; top: 108px;
    color: var(--ink); font-size: 32px;
  }
  .card--front .brand__mark { width: 13px; height: 13px; }

  .person {
    position: absolute; left: 84px; right: 62px; top: 206px; color: var(--ink);
  }
  .person__name {
    font-weight: 700; font-size: 30px; letter-spacing: 0.6px; line-height: 1.15;
  }
  .person__role-row { display: flex; align-items: flex-end; gap: 10px; }
  .person__role {
    font-weight: 700; font-size: 19px; line-height: 1.25; white-space: nowrap;
  }
  .role-rule { flex: 1; height: 1px; background: var(--rule); margin-bottom: 4px; }

  .contact {
    position: absolute; left: 66px; top: 280px; list-style: none;
    color: var(--ink-soft); font-size: 17px; line-height: 26px;
  }
  .contact__item { display: flex; align-items: center; gap: 12px; }
  .contact__icon { width: 12px; height: 12px; fill: var(--teal); flex: none; }
  .contact__strong { font-weight: 700; color: var(--ink); }

  .tagline {
    position: absolute; right: 62px; top: 342px; text-align: right;
    color: var(--ink-soft); font-size: 17px; line-height: 24px;
  }
</style>
</head>
<body>
<main class="canvas">
  <section class="card card--back" aria-label="Card back">
    <div class="brand"><span class="brand__mark"></span>form with marla</div>
  </section>

  <section class="card card--front" aria-label="Card front">
    <div class="brand"><span class="brand__mark"></span>form with marla</div>

    <div class="person">
      <p class="person__name">MARLA PRENTISS</p>
      <div class="person__role-row">
        <p class="person__role">BSc, Health &amp; Wellness Coach</p>
        <span class="role-rule"></span>
      </div>
    </div>

    <ul class="contact">
      <li class="contact__item">
        <svg class="contact__icon" viewBox="0 0 24 24" aria-hidden="true"><path d="M6.6 10.8a15.1 15.1 0 0 0 6.6 6.6l2.2-2.2a1 1 0 0 1 1-.25 11.4 11.4 0 0 0 3.6.57 1 1 0 0 1 1 1V20a1 1 0 0 1-1 1A17 17 0 0 1 3 4a1 1 0 0 1 1-1h3.5a1 1 0 0 1 1 1c0 1.25.2 2.45.57 3.57a1 1 0 0 1-.25 1z"/></svg>
        472-618-9043
      </li>
      <li class="contact__item">
        <svg class="contact__icon" viewBox="0 0 24 24" aria-hidden="true"><path d="M2 5h20v14H2z M2 5l10 8 10-8" stroke="#fff" stroke-width="1.5"/></svg>
        formwithmarla@quillpost.net
      </li>
      <li class="contact__item">
        <svg class="contact__icon" viewBox="0 0 24 24" aria-hidden="true"><circle cx="12" cy="12" r="10"/><path d="M2 12h20M12 2c3 3 3 17 0 20M12 2c-3 3-3 17 0 20" stroke="#fff" stroke-width="1.3" fill="none"/></svg>
        <span>www.<span class="contact__strong">formwithmarla</span>.net</span>
      </li>
    </ul>

    <p class="tagline">"Manifest your best"</p>
  </section>
</main>
</body>
</html>
```